WordPress Website Design for Multi-Brand Aviation Group (Unified Branding System)

Project Overview:
We are seeking a professional, modern WordPress website design for an aviation-focused umbrella company that owns and operates multiple subsidiary businesses. The goal is to create a cohesive visual system that clearly communicates that each company operates under the same parent organization, while still allowing each brand to maintain a slightly distinct identity.
This is not just a single website design—we are looking for a scalable design framework that can be applied across multiple aviation-related businesses.
Objectives:
- Establish a consistent, recognizable brand identity across all company websites
Clearly communicate the relationship between the parent company and its subsidiaries
-bCreate a clean, high-end corporate aviation aesthetic
- Ensure all designs are SEO-friendly and optimized for performance
- Allow flexibility for future expansion (additional subsidiaries)
- Target Audience:
- Corporate aviation clients
- Charter customers
- Students wishing to receive flight training
- Aircraft owners and operators
- Turbine aircraft training to meet insurance requirements
- Business professionals and high-net-worth individuals
- Aviation industry partners
Design Direction & Style:
We are looking for a premium, professional aviation feel—think clean, modern, and high-trust. The design should reflect the standards of corporate aviation: precision, safety, and sophistication.
Key style notes:
Minimalist but impactful layout
High-quality aviation photography (jets, interiors, operations, global travel)
Subtle motion/interaction (hover effects, transitions)
Clear typography hierarchy for readability and professionalism
Branding Requirements:
Incorporate the primary colors of the parent company logo across all designs
Website Structure (Core Pages):
Design a system that includes:
Home Page with the following links:
- About / Company Overview
- Aircraft Management
- Aircraft Acquisition
- Charter
- Pilot Services
- Trip Support
- Contact Page
Site should further include:
- Mobile-first responsive design
- Fast-loading, performance-optimized layouts
SEO & Technical Considerations:
- Design should support high-level SEO implementation:
- Clean layout structure that translates well to semantic HTML
- Proper heading hierarchy (H1, H2, H3)
- Space for keyword-rich content without clutter
- Optimized image placement (with alt text capability)
- Fast load times (lightweight design approach)
- Compatibility with WordPress SEO plugins (e.g., Yoast or Rank Math)
WordPress Requirements:
- Design should be easily built using WordPress (preferred builders: Elementor, Gutenberg, or similar)
- Reusable templates for scalability across multiple sites
- Easy for non-developers to update text and images
- Modular components (blocks/sections that can be reused across pages and sites)
- Navigation & UX:
- Simple, intuitive navigation
- Sticky header preferred
Style guide including:
- Colors
- Fonts
- Button styles
- Layout system
- Designs similar to high-end corporate aviation, private jet charter, or luxury service brands are preferred—clean, sharp, and premium without being overly flashy.
What We Want to Avoid:
- Overly busy layouts
- Generic templates with no brand identity
- Outdated or “stock” looking aviation designs
- Poor mobile responsiveness
Additional Notes:
We are building a long-term brand system, not just a one-off website. There is potential for ongoing work as we expand additional subsidiary sites.
We value designers who understand branding consistency across multiple business units and can create a scalable, professional system.
Include the attached main company logo "Vireton Aviation Group" and the "Member PJFO" logo on the main page.

```html
<!DOCTYPE html>
<html lang="en">
<head>
<meta charset="utf-8">
<title>Vireton Aviation Group</title>
<link href="https://fonts.googleapis.com/css2?family=Montserrat:wght@500;600;700&family=Inter:wght@400;500;600&display=swap" rel="stylesheet">
<style>
:root{
  --navy:#0b1a3d;
  --navy-deep:#0a1431;
  --blue:#0b36a8;
  --slate:#5b6b8c;
  --text:#0f172a;
  --muted:#5b6475;
  --light:#f4f6f9;
  --line:#e5e8ee;
  --white:#ffffff;
}
*{box-sizing:border-box;margin:0;padding:0}
html,body{width:1200px;height:5254px;overflow:hidden}
body{font-family:"Inter",sans-serif;color:var(--text);background:var(--white)}
h1,h2,h3,.display{font-family:"Montserrat",sans-serif}
section,header,footer{position:relative;width:1200px;overflow:hidden}
.wrap{position:absolute;left:112px;right:112px}
.eyebrow{font-size:11px;font-weight:600;letter-spacing:1.6px;text-transform:uppercase;color:var(--blue)}
.accent{color:var(--slate)}
.divider{width:82px;height:3px;background:var(--blue);margin:0 auto}
.btn{display:inline-flex;align-items:center;gap:8px;font-size:13px;font-weight:600;height:48px;padding:0 28px;border-radius:2px}
.btn-primary{background:var(--blue);color:var(--white)}
.btn-ghost{border:1.5px solid rgba(255,255,255,.7);color:var(--white)}
.brand{font-family:"Montserrat",sans-serif;font-weight:700;color:var(--blue);letter-spacing:.5px;display:flex;align-items:center;gap:8px}
.brand-dot{width:12px;height:12px;border-radius:50%;background:var(--blue)}

/* header */
.site-header{height:92px;display:flex;align-items:center;padding:0 112px;justify-content:space-between;background:var(--white)}
.site-header .brand{font-size:17px}
.nav{display:flex;gap:42px;font-size:12px;font-weight:500;margin-left:20px}
.site-header .btn{height:36px;font-size:12px;padding:0 22px}

/* hero */
.hero{height:588px;background:linear-gradient(100deg,#1d2433 0%,#384150 45%,#59606b 100%)}
.hero .wrap{top:36px}
.pill{display:inline-flex;align-items:center;gap:10px;height:46px;padding:0 18px;border-radius:23px;background:rgba(255,255,255,.22);color:var(--navy);font-family:"Montserrat",sans-serif;font-weight:600;font-size:19px;letter-spacing:1px}
.pill small{font-size:9px;letter-spacing:0;font-weight:500;display:block;margin-bottom:-4px}
.pill .circle{width:30px;height:30px;border-radius:50%;background:var(--navy)}
.hero h1{margin-top:24px;font-size:62px;line-height:78px;font-weight:700;color:var(--white)}
.hero h1 span{color:#a9b1c0}
.hero p{margin-top:22px;width:650px;font-size:16px;line-height:28px;color:#d9dde5}
.hero .actions{margin-top:38px;display:flex;gap:14px}
.hero .btn-primary{width:190px;justify-content:center}
.hero .btn-ghost{width:132px;justify-content:center}

/* intro */
.intro{height:636px}
.intro .wrap{top:84px;width:500px}
.intro h2{margin-top:20px;font-size:42px;line-height:52px;font-weight:700}
.intro p{margin-top:54px;font-size:15px;line-height:25px;color:var(--muted);width:450px}
.quote{margin-top:26px;border-left:3px solid var(--blue);padding:4px 0 4px 16px;font-size:15px;line-height:25px;color:var(--muted)}
.stats{margin-top:42px;display:flex;gap:70px}
.stat b{font-family:"Montserrat",sans-serif;font-size:30px;font-weight:700;display:block}
.stat span{font-size:11px;letter-spacing:1.3px;color:var(--muted)}
.intro-photo{position:absolute;left:635px;top:81px;width:565px;height:470px;background:linear-gradient(135deg,#3f6fc4 0%,#8a8f86 55%,#4c4f52 100%)}

/* services */
.services{height:954px;background:var(--light);text-align:center}
.section-head{position:absolute;left:0;right:0;top:88px;text-align:center}
.section-head h2{margin:14px auto 26px;font-size:42px;line-height:44px;font-weight:700}
.cards{position:absolute;left:96px;width:1006px;top:274px;display:grid;grid-template-columns:repeat(3,1fr);gap:29px 28px;text-align:left}
.card{background:var(--white);height:296px;padding:40px 34px;box-shadow:0 2px 10px rgba(15,23,42,.06)}
.icon-ring{width:50px;height:50px;border-radius:50%;background:var(--light);display:flex;align-items:center;justify-content:center}
.icon-ring svg{width:22px;height:22px;stroke:var(--blue);fill:none;stroke-width:1.8;stroke-linecap:round;stroke-linejoin:round}
.card h3{margin-top:30px;font-size:20px;font-weight:600}
.card p{margin-top:14px;font-size:13px;line-height:23px;color:var(--muted)}
.card a{display:inline-block;margin-top:22px;font-size:11px;font-weight:700;letter-spacing:1px;color:var(--blue);text-decoration:none}

/* why */
.why{height:512px}
.why .section-head{top:86px}
.features{position:absolute;left:80px;width:1040px;top:300px;display:grid;grid-template-columns:repeat(4,1fr);text-align:center}
.feature .icon-ring{width:70px;height:70px;margin:0 auto}
.feature .icon-ring svg{width:26px;height:26px}
.feature h3{margin-top:20px;font-size:16px;font-weight:600}
.feature p{margin:10px auto 0;width:230px;font-size:12px;line-height:20px;color:var(--muted)}

/* lifestyle */
.lifestyle{height:528px;background:linear-gradient(100deg,#0f1a36 0%,#1b2745 50%,#3a4357 100%)}
.lifestyle .wrap{left:96px;top:118px}
.lifestyle .eyebrow{color:#3f5fc7}
.lifestyle h2{margin-top:14px;font-size:42px;line-height:50px;font-weight:700;color:var(--white)}
.lifestyle h2 span{color:#a9b1c0}
.lifestyle p{margin-top:28px;width:620px;font-size:16px;line-height:28px;color:#d6dbe4}
.lifestyle .row{margin-top:38px;display:flex;align-items:center;gap:80px}
.lifestyle .btn{height:42px;font-size:12px}
.tagline{font-size:12px;letter-spacing:2px;color:#9aa3b5}

/* who */
.who{height:518px;background:var(--light)}
.who .wrap{top:90px;width:480px}
.who h2{margin-top:22px;font-size:42px;font-weight:700}
.who p{margin-top:24px;font-size:15px;line-height:25px;color:var(--muted)}
.checks{margin-top:34px;display:grid;grid-template-columns:240px 240px;row-gap:14px;font-size:13px;font-weight:500}
.checks li{list-style:none;display:flex;align-items:center;gap:10px}
.checks svg{width:16px;height:16px;stroke:var(--blue);fill:none;stroke-width:1.8}
.photo{position:absolute;box-shadow:0 6px 20px rgba(15,23,42,.2)}
.photo-cabin{left:627px;top:135px;width:224px;height:218px;background:linear-gradient(180deg,#c9ccd2 0%,#4a5a7a 60%,#1f2b46 100%)}
.photo-pilot{left:865px;top:163px;width:225px;height:219px;background:linear-gradient(160deg,#3c5ab0 0%,#c8453e 50%,#5a4b3a 100%)}

/* industry */
.industry{height:462px;text-align:center}
.industry .section-head{top:90px}
.industry p{margin:-8px auto 38px;width:660px;font-size:15px;line-height:26px;color:var(--muted)}
.affiliates{position:absolute;left:0;right:0;top:348px;display:flex;justify-content:center;gap:150px;align-items:center}
.affiliates .brand{font-size:22px}
.affiliates .brand.navy{color:var(--navy)}
.affiliates .navy .brand-dot{background:var(--navy)}

/* cta */
.cta{height:604px;background:linear-gradient(180deg,#0f1d42 0%,#0b1533 100%)}
.cta-panel{position:absolute;left:235px;top:108px;width:735px;height:448px;border:1px solid rgba(255,255,255,.07);background:rgba(255,255,255,.02);text-align:center;padding-top:56px}
.cta .eyebrow{color:#2e4fb8}
.cta h2{margin-top:20px;font-size:42px;line-height:42px;font-weight:700;color:var(--white)}
.cta p{margin:22px auto 0;width:590px;font-size:16px;line-height:28px;color:#d6dbe4}
.cta .actions{margin-top:42px;display:flex;justify-content:center;gap:14px}
.cta .btn{height:48px;font-size:12px}
.btn-light{background:var(--white);color:var(--text)}

/* footer */
.site-footer{height:360px;background:var(--navy-deep);color:#c4cadb}
.footer-brand{position:absolute;left:112px;top:80px}
.footer-brand .brand{color:var(--white);font-size:18px}
.footer-brand .brand-dot{background:var(--white)}
.footer-brand p{margin-top:44px;width:330px;font-size:11px;line-height:19px;color:#7f89a3}
.socials{margin-top:22px;display:flex;gap:24px}
.socials span{width:22px;height:22px;border:1.5px solid #c4cadb;border-radius:4px}
.fcol{position:absolute;top:62px;font-size:11px}
.fcol h4{font-family:"Inter",sans-serif;font-size:11px;font-weight:600;letter-spacing:1.2px;color:var(--white);margin-bottom:20px}
.fcol li{list-style:none;margin-bottom:12px;display:flex;gap:10px}
.fcol svg{width:14px;height:14px;stroke:#5b7ae0;fill:none;stroke-width:1.8;flex:none}
.footer-bottom{position:absolute;left:112px;right:112px;top:286px;border-top:1px solid rgba(255,255,255,.06);padding-top:14px;font-size:10px;color:#58627d;display:flex;justify-content:space-between}
.footer-bottom span+span{margin-left:22px}
</style>
</head>
<body>

<header class="site-header">
  <div class="brand"><span class="brand-dot"></span>VIRETON AVIATION GROUP</div>
  <nav class="nav"><span>Home</span><span>About</span><span>Aircraft Management</span><span>Aircraft Acquisition</span><span>Charter</span><span>More</span></nav>
  <span class="btn btn-primary">Request Consultation</span>
</header>

<section class="hero" role="img" aria-label="Photograph of a private jet on approach against an overcast sky">
  <div class="wrap">
    <span class="pill"><span class="circle"></span><span><small>member of</small>PJFO</span></span>
    <h1>Elevating Aviation<br><span>Ownership, Charter &amp;<br>Flight Solutions</span></h1>
    <p>Vireton Aviation Group delivers premium aviation services through a network of trusted subsidiaries specializing in aircraft management, charter, acquisitions, pilot services, and trip support.</p>
    <div class="actions">
      <span class="btn btn-primary">Explore Services <svg width="12" height="12" viewBox="0 0 12 12" fill="none" stroke="currentColor" stroke-width="1.6"><path d="M1 6h10M7 2l4 4-4 4"/></svg></span>
      <span class="btn btn-ghost">Contact Us</span>
    </div>
  </div>
</section>

<section class="intro">
  <div class="wrap">
    <div class="eyebrow">Parent Company Introduction</div>
    <h2>One Aviation Group.<br><span class="accent">Multiple Specialized<br>Solutions.</span></h2>
    <p>Vireton Aviation Group is a modern aviation holding company built to serve aircraft owners, charter clients, flight students, and aviation professionals through a unified network of specialized businesses.</p>
    <div class="quote">We combine operational excellence, safety, and premium service standards across every division.</div>
    <div class="stats">
      <div class="stat"><b>24/7</b><span>GLOBAL SUPPORT</span></div>
      <div class="stat"><b>100%</b><span>SAFETY RECORD</span></div>
    </div>
  </div>
  <div class="intro-photo" role="img" aria-label="Photograph of a pilot in headset standing before a blue jet aircraft"></div>
</section>

<section class="services">
  <div class="section-head">
    <div class="eyebrow">Our Aviation Companies &amp; Services</div>
    <h2>Comprehensive Solutions<br>Under One Network</h2>
    <div class="divider"></div>
  </div>
  <div class="cards">
    <article class="card"><div class="icon-ring"><svg viewBox="0 0 24 24"><path d="M12 3l7 3v6c0 4-3 7-7 9-4-2-7-5-7-9V6z"/><path d="M9 12l2 2 4-4"/></svg></div><h3>Aircraft Management</h3><p>Professional oversight, operations, maintenance coordination, and owner support.</p><a>LEARN MORE →</a></article>
    <article class="card"><div class="icon-ring"><svg viewBox="0 0 24 24"><circle cx="12" cy="12" r="8"/><path d="M12 2v5M12 17v5M2 12h5M17 12h5"/></svg></div><h3>Aircraft Acquisition</h3><p>Strategic sourcing, evaluations, negotiations, and seamless ownership transitions.</p><a>LEARN MORE →</a></article>
    <article class="card"><div class="icon-ring"><svg viewBox="0 0 24 24"><path d="M21 3L3 10l8 3 3 8z"/></svg></div><h3>Charter Services</h3><p>Private charter solutions tailored for business and leisure travel.</p><a>LEARN MORE →</a></article>
    <article class="card"><div class="icon-ring"><svg viewBox="0 0 24 24"><circle cx="9" cy="8" r="3.5"/><path d="M3 20c0-3.5 2.7-6 6-6s6 2.5 6 6"/><path d="M16 4.5a3.5 3.5 0 010 7M18 14c2 .8 3 3 3 6"/></svg></div><h3>Pilot Services</h3><p>Experienced pilot staffing, training support, and flight crew solutions.</p><a>LEARN MORE →</a></article>
    <article class="card"><div class="icon-ring"><svg viewBox="0 0 24 24"><path d="M12 21s-7-6.5-7-11a7 7 0 0114 0c0 4.5-7 11-7 11z"/><circle cx="12" cy="10" r="2.5"/></svg></div><h3>Trip Support</h3><p>Worldwide logistics, permits, scheduling, fuel, and concierge coordination.</p><a>LEARN MORE →</a></article>
    <article class="card"><div class="icon-ring"><svg viewBox="0 0 24 24"><path d="M2 9l10-5 10 5-10 5z"/><path d="M6 11v5c3 2 9 2 12 0v-5"/></svg></div><h3>Flight Training</h3><p>Professional turbine and advanced aircraft training programs.</p><a>LEARN MORE →</a></article>
  </div>
</section>

<section class="why">
  <div class="section-head">
    <div class="eyebrow">Why Choose Vireton</div>
    <h2>Built for Owners.<br><span class="accent">Trusted by Professionals.</span></h2>
    <div class="divider"></div>
  </div>
  <div class="features">
    <div class="feature"><div class="icon-ring"><svg viewBox="0 0 24 24"><path d="M12 3l7 3v6c0 4-3 7-7 9-4-2-7-5-7-9V6z"/><path d="M12 9v4M12 16v.5"/></svg></div><h3>Safety First</h3><p>Commitment to operational discipline and industry best practices.</p></div>
    <div class="feature"><div class="icon-ring"><svg viewBox="0 0 24 24"><path d="M10 4l1.5 5 5 1.5-5 1.5L10 17l-1.5-5-5-1.5 5-1.5z"/><path d="M18 3v4M16 5h4M17 16v4M15 18h4"/></svg></div><h3>Premium Service</h3><p>White-glove client experience from inquiry to arrival.</p></div>
    <div class="feature"><div class="icon-ring"><svg viewBox="0 0 24 24"><circle cx="12" cy="9" r="5"/><path d="M9 13.5L8 21l4-2 4 2-1-7.5"/></svg></div><h3>Industry Expertise</h3><p>Experienced leadership across aviation sectors.</p></div>
    <div class="feature"><div class="icon-ring"><svg viewBox="0 0 24 24"><path d="M12 3l9 5-9 5-9-5z"/><path d="M3 12l9 5 9-5M3 16l9 5 9-5"/></svg></div><h3>Scalable Solutions</h3><p>Flexible support for individuals, corporations, and fleets.</p></div>
  </div>
</section>

<section class="lifestyle" role="img" aria-label="Photograph of a business jet parked on the apron at dusk">
  <div class="wrap">
    <div class="eyebrow">Aviation Lifestyle</div>
    <h2>Corporate Aviation<br><span>Without Compromise</span></h2>
    <p>From executive travel to aircraft ownership support, Vireton Aviation Group creates efficient, private, and dependable aviation experiences tailored to your exact standards.</p>
    <div class="row"><span class="btn btn-primary">Experience Vireton</span><span class="tagline">EXCELLENCE IN FLIGHT</span></div>
  </div>
</section>

<section class="who">
  <div class="wrap">
    <div class="eyebrow">Client Portfolio</div>
    <h2>Who We Serve</h2>
    <p>Our diverse client base trusts Vireton Aviation Group to deliver tailored aviation solutions. Whether you are managing an asset, learning to fly, or planning your next corporate charter, our specialized subsidiaries have you covered.</p>
    <ul class="checks">
      <li><svg viewBox="0 0 16 16"><circle cx="8" cy="8" r="6.5"/><path d="M5 8l2 2 4-4"/></svg>Aircraft Owners</li>
      <li><svg viewBox="0 0 16 16"><circle cx="8" cy="8" r="6.5"/><path d="M5 8l2 2 4-4"/></svg>Charter Travelers</li>
      <li><svg viewBox="0 0 16 16"><circle cx="8" cy="8" r="6.5"/><path d="M5 8l2 2 4-4"/></svg>Corporate Executives</li>
      <li><svg viewBox="0 0 16 16"><circle cx="8" cy="8" r="6.5"/><path d="M5 8l2 2 4-4"/></svg>High-Net-Worth Individuals</li>
      <li><svg viewBox="0 0 16 16"><circle cx="8" cy="8" r="6.5"/><path d="M5 8l2 2 4-4"/></svg>Flight Students</li>
      <li><svg viewBox="0 0 16 16"><circle cx="8" cy="8" r="6.5"/><path d="M5 8l2 2 4-4"/></svg>Insurance Training Clients</li>
      <li><svg viewBox="0 0 16 16"><circle cx="8" cy="8" r="6.5"/><path d="M5 8l2 2 4-4"/></svg>Aviation Partners</li>
    </ul>
  </div>
  <div class="photo photo-cabin" role="img" aria-label="Photograph of a passenger cabin aisle with blue seats"></div>
  <div class="photo photo-pilot" role="img" aria-label="Photograph of a pilot holding a helmet beside a red aircraft"></div>
</section>

<section class="industry">
  <div class="section-head">
    <div class="eyebrow">Memberships &amp; Affiliations</div>
    <h2>Industry Connected</h2>
    <p>Proudly aligned with leading aviation organizations and industry best practices to ensure safety, efficiency, and premier service across our network.</p>
    <div class="divider"></div>
  </div>
  <div class="affiliates">
    <div class="brand"><span class="brand-dot"></span>VIRETON</div>
    <div class="brand navy"><span class="brand-dot"></span>PJFO</div>
  </div>
</section>

<section class="cta">
  <div class="cta-panel">
    <div class="eyebrow">Get In Touch</div>
    <h2>Ready to Elevate Your<br>Aviation Experience?</h2>
    <p>Speak with our team today to discuss tailored solutions for ownership, charter, management, or professional training.</p>
    <div class="actions"><span class="btn btn-light">Contact Us</span><span class="btn btn-primary">Schedule Consultation</span></div>
  </div>
</section>

<footer class="site-footer">
  <div class="footer-brand">
    <div class="brand"><span class="brand-dot"></span>VIRETON AVIATION GROUP</div>
    <p>Elevating aviation ownership, charter, and flight solutions through a network of trusted subsidiaries dedicated to safety, service, and excellence.</p>
    <div class="socials"><span></span><span></span></div>
  </div>
  <div class="fcol" style="left:512px"><h4>COMPANY</h4><ul><li>About</li><li>Contact</li><li>Careers</li></ul></div>
  <div class="fcol" style="left:714px"><h4>SERVICES</h4><ul><li>Management</li><li>Charter</li><li>Acquisition</li><li>Pilot Services</li></ul></div>
  <div class="fcol" style="left:914px"><h4>CONTACT</h4><ul>
    <li><svg viewBox="0 0 16 16"><path d="M3 2h3l1.5 3.5-2 1.2a8 8 0 004 4l1.2-2L14 10v3a1 1 0 01-1 1A11 11 0 012 3a1 1 0 011-1z"/></svg>+1 (800) 555-0142</li>
    <li><svg viewBox="0 0 16 16"><rect x="2" y="3.5" width="12" height="9" rx="1"/><path d="M2 4l6 5 6-5"/></svg>info@viretonaviation.com</li>
    <li><svg viewBox="0 0 16 16"><path d="M8 14s-5-4.5-5-8a5 5 0 0110 0c0 3.5-5 8-5 8z"/><circle cx="8" cy="6" r="1.6"/></svg><span>Global Headquarters<br>Skyline Drive, Suite 100</span></li>
  </ul></div>
  <div class="footer-bottom"><span>© 2026 Vireton Aviation Group. All Rights Reserved.</span><div><span>Privacy Policy</span><span>Terms of Service</span></div></div>
</footer>

</body>
</html>
```